Doctor to Patient Management Website

I need a design for a health management website that connects doctors to patients. The website will consist of: A main page mainly describing our goal, services, and initiatives towards (Who we are AKA "About Us", Our services, Contact Us, Quick Links for health tips, Language selection, Find a doctor, search bar, Member Login Section, small glossary section below with links to all entities mentioned prior, Help section (Helpful tips and tutorials, Used to request help from admin, customer service, to resolve issues or get assistance). A profile page with two types:1) Doctor Profile: Doctor Personal info (First, Last, Middle Name, Title), Clinic, Hospital Info, Department, Credentials, Years of Experience, Patients rating, #Patients seen during the current week, #Patients seen in total, Picture, Link to email doctor, Link to print doctor's profile). Tabs for "About Me", "Contact Info", "Ratings & Comments", "Documents" (To be downloaded and uploaded by patient), "Patients (List of Patients alphabetical order by name)", "Calendar" (to see doctor's availability for booking) underneath all links. 2) Patient profile: About me, Personal Info, Height, Weight, Blood Type, Age, DOB, Name, etc..., Message and email link.Picture of patient with menu made of "Personal Data", "Biometrics", "Allergies", "Illnesses", "Medications", "Medical Procedures", "Doctors" treating the patient, "Documents" (To be downloaded and uploaded by patient). Underneath all, other patients he or she is related to (For example: family member, so patient can't connect to other patients who are family members)3) Login section: New Users will have option to register using:First Name (Required), Last Name, Middle (not required), Address (Not required), City (Required), Country (Required), Email (Not required), Phone Number (Required), Choose UserName, Password, Account Type (Doctor or Patient). Once registered, they will log in using UserName, Password, and Account_Type.Curent Users will log in using UserName, Password, and Account_Type and option to retrieve username or password.Pages to include (Login Page - Registration Page - Retrieve Username and Reset Password Page)Please see link below:https://plumcrate-adwerks.net/importance-claiming-vantorix-quibble-zarn/Pictures are attached to this project as an inspirationFYI: Dummy text can be used to fill in the business, services, and descriptive information. Feel free to include your own ideas in the layout, design, categories, patterns, and more to and showcase your talent. Design and pictures provided are available as source of ideas.

Target Market(s)

Age: 21+ / Family Oriented / Medical Sector / Metropolitan Area / Educated and non Educated Users

Industry/Entity Type

Health Care

Number of Pages Required

5+ page

Font styles to use
Sans Serif

Colors

Designer to choose colors to be used in the design.

Requirements
Must have
• Thin layer design
• Simple font - No serif
• Clean menu with light but solid colors (No Gradient effect)
Nice to have
• Different color themes (2 or 3) can be combined
• Sample pictures for illustration (either as an ad or to go with the flow of your design)
• Dashboard Feel (Suggested but not required)
Should not have
• Artistic fonts - with Serif
• Dark color themes

```html
<!DOCTYPE html>
<html lang="en">
<head>
<meta charset="utf-8">
<title>Velmora – Doctor to Patient Management</title>
<link href="https://fonts.googleapis.com/css2?family=Raleway:wght@600;700;800&family=Open+Sans:wght@400;600;700&display=swap" rel="stylesheet">
<style>
:root{
  --blue:#2f8fdf;
  --teal:#16a596;
  --ink:#222a33;
  --text:#55606b;
  --light:#f3f8fd;
  --tint:#ddeefa;
  --footer:#e7f1fb;
  --line:#d6dfe8;
  --white:#ffffff;
}
*{box-sizing:border-box;margin:0;padding:0}
html,body{width:1200px;height:3614px;overflow:hidden}
body{position:relative;background:var(--white);font-family:'Open Sans',sans-serif;color:var(--text)}
.abs{position:absolute}
.heading{font-family:'Raleway',sans-serif;font-weight:800;color:var(--ink);letter-spacing:.5px}
.eyebrow{font-family:'Raleway',sans-serif;font-weight:600;color:var(--blue);font-size:19px;letter-spacing:.5px}
.btn-outline{position:absolute;border:2px solid var(--teal);border-radius:30px;color:var(--teal);font-weight:700;font-size:15px;display:flex;align-items:center;justify-content:center;letter-spacing:.5px;background:transparent}
.para{font-size:14px;line-height:30px;color:var(--text)}

/* header */
.site-header{top:0;left:0;width:1200px;height:130px;background:var(--white)}
.brand{font-family:'Raleway',sans-serif;font-weight:800;color:var(--ink);font-size:38px;letter-spacing:1px}
.member-login{left:829px;top:14px;width:176px;height:54px;border:2px solid var(--teal);border-radius:28px;color:var(--teal);font-weight:700;font-size:14px;display:flex;align-items:center;justify-content:center;gap:7px}
.lang{left:1038px;top:31px;display:flex;align-items:center;gap:10px}
.lang-swatch{width:28px;height:18px;background:#3d5a9e;border-radius:2px}
.main-nav{left:530px;top:88px;display:flex;gap:32px;font-family:'Raleway',sans-serif;font-weight:700;font-size:15px;color:var(--ink)}
.main-nav .active{color:var(--blue)}

/* hero */
.hero{top:130px;left:0;width:1200px;height:526px;background:var(--blue);overflow:hidden}
.hero-title{left:111px;top:108px;font-family:'Raleway',sans-serif;font-weight:800;font-size:45px;line-height:58px;color:var(--white)}
.hero-sub{left:111px;top:246px;width:480px;font-size:18px;line-height:34px;color:var(--white);font-weight:600}
.search{left:111px;top:345px;width:494px;height:56px;display:flex}
.search-field{flex:1;background:var(--white);display:flex;align-items:center;padding-left:22px;gap:10px;font-size:15px;color:#6a737c}
.search-btn{width:66px;background:var(--teal);display:flex;align-items:center;justify-content:center}
.hero-photo{left:607px;top:-51px;width:584px;height:584px;border-radius:50%;background:radial-gradient(circle at 40% 45%,#f3e6df,#d9e3ea 55%,#b9c9d6);border:4px solid var(--white)}

/* about */
.about-eyebrow{left:111px;top:782px}
.about-title{left:111px;top:820px;font-size:40px}
.about-text{left:455px;top:728px;width:635px}
.about-text p+p{margin-top:20px}

/* services */
.services{top:1125px;left:0;width:1200px;height:887px;background:var(--light)}
.center{width:1200px;text-align:center;left:0}
.card{position:absolute;width:467px;height:182px;background:var(--white);border:2px solid #e2e7ec;border-radius:6px}
.card svg{position:absolute;left:34px;top:30px}
.card h3{position:absolute;left:110px;top:30px;font-family:'Raleway',sans-serif;font-weight:700;font-size:20px;color:var(--ink);letter-spacing:.5px}
.card p{position:absolute;left:110px;top:66px;width:330px;font-size:14px;line-height:28px}
.card .more{position:absolute;left:110px;top:136px;font-size:14px;font-weight:700;color:var(--teal)}

/* tips */
.tips{top:2012px;left:0;width:1200px;height:514px;background:var(--tint)}
.tips-photo{left:600px;top:0;width:600px;height:514px;background:linear-gradient(135deg,#e9e1d6,#f5f2ee 45%,#cfd8df)}
.ticks{list-style:none}
.ticks li{display:flex;align-items:center;gap:14px;font-size:15px;height:33px;color:#4c5660}

/* help */
.video{left:111px;top:2781px;width:446px;height:294px;background:linear-gradient(120deg,#dfe6ec,#f2f4f6 50%,#c9d3dc)}
.play{left:298px;top:2897px}

/* footer */
.footer{top:3186px;left:0;width:1200px;height:428px;background:var(--footer)}
.foot-h{font-family:'Raleway',sans-serif;font-weight:700;font-size:19px;color:var(--ink)}
.foot-links{list-style:none;font-size:14px;line-height:32px;color:#4c5660}
.email-input{left:576px;top:3363px;width:253px;height:34px;background:var(--white);border:1px solid var(--line);font-size:13px;padding-left:12px;display:flex;align-items:center;color:#555}
.subscribe{left:576px;top:3417px;width:125px;height:46px;border-radius:24px;background:var(--teal);color:var(--white);font-weight:700;font-size:14px;display:flex;align-items:center;justify-content:center}
.contact-row{display:flex;gap:16px;font-size:14px;line-height:28px;color:#4c5660}
.divider{left:111px;top:3509px;width:979px;height:1px;background:var(--line)}
.social{width:34px;height:34px;border:2px solid var(--blue);border-radius:50%}
</style>
</head>
<body>

<header class="site-header abs">
  <div class="brand abs" style="left:111px;top:38px">VELMORA</div>
  <div class="member-login abs">
    <svg width="12" height="13" viewBox="0 0 12 13"><circle cx="6" cy="3.5" r="3" fill="#16a596"/><path d="M0 13c0-4 2.5-6 6-6s6 2 6 6z" fill="#16a596"/></svg>
    MEMBER LOGIN
  </div>
  <div class="lang abs"><span class="lang-swatch"></span>
    <svg width="10" height="6" viewBox="0 0 10 6"><path d="M1 1l4 4 4-4" stroke="#444" stroke-width="1.5" fill="none"/></svg>
  </div>
  <nav class="main-nav abs">
    <span class="active">HOME</span><span>ABOUT US</span><span>OUR SERVICES</span><span>PROFILE</span><span>CONTACT US</span>
  </nav>
</header>

<section class="hero abs">
  <h1 class="hero-title abs">DOCTOR TO PATIENT<br>MANAGEMENT</h1>
  <p class="hero-sub abs">Nam libero tempore, cum soluta nobis est eligendi optio cumque nihil impero tedit qu.</p>
  <div class="search abs">
    <div class="search-field">
      <svg width="14" height="15" viewBox="0 0 12 13"><circle cx="6" cy="3.5" r="3" fill="#777"/><path d="M0 13c0-4 2.5-6 6-6s6 2 6 6z" fill="#777"/></svg>
      Find a doctor
    </div>
    <div class="search-btn">
      <svg width="22" height="22" viewBox="0 0 22 22"><circle cx="9" cy="9" r="6.5" stroke="#fff" stroke-width="3" fill="none"/><path d="M14 14l6 6" stroke="#fff" stroke-width="3.5" stroke-linecap="round"/></svg>
    </div>
  </div>
  <div class="hero-photo abs" role="img" aria-label="Photo of a doctor consulting with a patient at a desk"></div>
</section>

<div class="eyebrow abs about-eyebrow">ABOUT US</div>
<h2 class="heading abs about-title">WHO WE ARE</h2>
<div class="about-text abs para">
  <p>At vero eos et accusamus et iusto odio dignissimos ducimus qui blanditiis praesentium voluptatum delenti atque corrupti quos dolores et quas molestias exce.</p>
  <p>turi sint occaecati cupiditate non provi dent, similique sunt in culpa qui officia deserunt mollitia ani mi, id est laborum et dolorum fuga. Eth arum quidem rerum facilis est et expedita distinctio volupt as assumenda est, omnis dolor repellend poribus autem quibusdam et aut officiis debitis aut reum necessitatibus saepe eveit ut et voluptates repudiand.</p>
</div>
<div class="btn-outline" style="left:455px;top:968px;width:164px;height:56px">READ MORE</div>

<section class="services abs">
  <div class="eyebrow abs center" style="top:86px">OUR SERVICES</div>
  <h2 class="heading abs center" style="top:120px;font-size:40px">WHAT WE DO</h2>

  <div class="card" style="left:111px;top:232px">
    <svg width="48" height="44" viewBox="0 0 48 44"><rect x="15" y="2" width="18" height="9" rx="2" fill="none" stroke="#2f8fdf" stroke-width="3"/><rect x="2" y="10" width="44" height="32" rx="4" fill="#2f8fdf"/><path d="M20 19h8v6h6v8h-6v6h-8v-6h-6v-8h6z" fill="#fff" transform="translate(0 -3) scale(1 .95)"/></svg>
    <h3>HEALTH SURVEILLANCE</h3>
    <p>At vero eos et accusamus et iusto odio dignios ducimus qui blanqui officditis praese.</p>
    <span class="more">READ MORE</span>
  </div>
  <div class="card" style="left:622px;top:232px">
    <svg width="50" height="44" viewBox="0 0 50 44"><path d="M25 42L6 23C-2 15 3 2 13 2c5 0 9 3 12 7 3-4 7-7 12-7 10 0 15 13 7 21z" fill="#2f8fdf"/><path d="M2 22h14l4-8 6 16 4-8h18" stroke="#fff" stroke-width="3" fill="none"/></svg>
    <h3>WELLBEING</h3>
    <p>At vero eos et accusamus et iusto odio dignios ducimus qui blanqui officditis praese.</p>
    <span class="more">READ MORE</span>
  </div>
  <div class="card" style="left:111px;top:461px">
    <svg width="44" height="46" viewBox="0 0 44 46"><circle cx="22" cy="11" r="9" fill="#2f8fdf"/><path d="M2 46c0-13 8-22 20-22s20 9 20 22z" fill="#2f8fdf"/><circle cx="16" cy="36" r="4" fill="none" stroke="#fff" stroke-width="2.5"/><path d="M16 26v6M28 26v10a3 3 0 0 1-6 0" stroke="#fff" stroke-width="2.5" fill="none"/></svg>
    <h3>PRIMARY CARE</h3>
    <p>At vero eos et accusamus et iusto odio dignios ducimus qui blanqui officditis praese.</p>
    <span class="more">READ MORE</span>
  </div>
  <div class="card" style="left:622px;top:461px">
    <svg width="52" height="44" viewBox="0 0 52 44"><path d="M3 2v40h47" stroke="#2f8fdf" stroke-width="3" fill="none"/><path d="M8 34l12-13 9 8 16-18" stroke="#2f8fdf" stroke-width="4" fill="none"/><path d="M38 9h9v9z" fill="#2f8fdf"/></svg>
    <h3>HEALTHCARE ANALYTICS</h3>
    <p>At vero eos et accusamus et iusto odio dignios ducimus qui blanqui officditis praese.</p>
    <span class="more">READ MORE</span>
  </div>

  <div class="btn-outline" style="left:519px;top:723px;width:163px;height:56px">VIEW MORE</div>
</section>

<section class="tips abs">
  <div class="eyebrow abs" style="left:111px;top:82px">KEY BENEFITS</div>
  <h2 class="heading abs" style="left:111px;top:118px;font-size:40px">HEALTH TIPS</h2>
  <ul class="ticks abs" style="left:111px;top:200px">
    <li><svg width="16" height="16" viewBox="0 0 16 16"><circle cx="8" cy="8" r="8" fill="#2f8fdf"/><path d="M4.5 8.3l2.3 2.2 4.7-4.8" stroke="#fff" stroke-width="2" fill="none"/></svg>Nam libero tempore, cum soluta nobis est eligendi optio cum</li>
    <li><svg width="16" height="16" viewBox="0 0 16 16"><circle cx="8" cy="8" r="8" fill="#2f8fdf"/><path d="M4.5 8.3l2.3 2.2 4.7-4.8" stroke="#fff" stroke-width="2" fill="none"/></svg>Que nihil impedit quo minus id quod maxime placeat facere</li>
    <li><svg width="16" height="16" viewBox="0 0 16 16"><circle cx="8" cy="8" r="8" fill="#2f8fdf"/><path d="M4.5 8.3l2.3 2.2 4.7-4.8" stroke="#fff" stroke-width="2" fill="none"/></svg>Possimus, omnis voluptas assumenda est, omnis dolor repel</li>
    <li><svg width="16" height="16" viewBox="0 0 16 16"><circle cx="8" cy="8" r="8" fill="#2f8fdf"/><path d="M4.5 8.3l2.3 2.2 4.7-4.8" stroke="#fff" stroke-width="2" fill="none"/></svg>Temporibus autem quibusdam et aut officiis debitismigenn</li>
    <li><svg width="16" height="16" viewBox="0 0 16 16"><circle cx="8" cy="8" r="8" fill="#2f8fdf"/><path d="M4.5 8.3l2.3 2.2 4.7-4.8" stroke="#fff" stroke-width="2" fill="none"/></svg>Aut rerum necessitatibus saepe eveniet ut et voluptates repu</li>
  </ul>
  <div class="btn-outline" style="left:111px;top:410px;width:164px;height:56px">READ MORE</div>
  <div class="tips-photo abs" role="img" aria-label="Photo of a doctor writing notes for a patient beside a fruit bowl and stethoscope"></div>
</section>

<div class="eyebrow abs center" style="top:2636px">TUTORIALS</div>
<h2 class="heading abs center" style="top:2672px;font-size:40px">HELP</h2>
<div class="video abs" role="img" aria-label="Video thumbnail of a doctor using a tablet"></div>
<svg class="play abs" width="64" height="64" viewBox="0 0 64 64"><circle cx="32" cy="32" r="29" fill="rgba(40,40,40,.55)" stroke="#fff" stroke-width="4"/><path d="M25 19l22 13-22 13z" fill="#fff"/></svg>
<ul class="ticks abs" style="left:645px;top:2790px">
  <li><svg width="16" height="16" viewBox="0 0 16 16"><circle cx="8" cy="8" r="8" fill="#2f8fdf"/><path d="M4.5 8.3l2.3 2.2 4.7-4.8" stroke="#fff" stroke-width="2" fill="none"/></svg>Nam libero tempore, cum soluta nobis est eligendi optio cum</li>
  <li><svg width="16" height="16" viewBox="0 0 16 16"><circle cx="8" cy="8" r="8" fill="#2f8fdf"/><path d="M4.5 8.3l2.3 2.2 4.7-4.8" stroke="#fff" stroke-width="2" fill="none"/></svg>Que nihil impedit quo minus id quod maxime placeat facere</li>
  <li><svg width="16" height="16" viewBox="0 0 16 16"><circle cx="8" cy="8" r="8" fill="#2f8fdf"/><path d="M4.5 8.3l2.3 2.2 4.7-4.8" stroke="#fff" stroke-width="2" fill="none"/></svg>Possimus, omnis voluptas assumenda est, omnis dolor repel</li>
  <li><svg width="16" height="16" viewBox="0 0 16 16"><circle cx="8" cy="8" r="8" fill="#2f8fdf"/><path d="M4.5 8.3l2.3 2.2 4.7-4.8" stroke="#fff" stroke-width="2" fill="none"/></svg>Temporibus autem quibusdam et aut officiis debitismigenn</li>
  <li><svg width="16" height="16" viewBox="0 0 16 16"><circle cx="8" cy="8" r="8" fill="#2f8fdf"/><path d="M4.5 8.3l2.3 2.2 4.7-4.8" stroke="#fff" stroke-width="2" fill="none"/></svg>Aut rerum necessitatibus saepe eveniet ut et voluptates repu</li>
</ul>
<div class="btn-outline" style="left:645px;top:2996px;width:164px;height:56px">READ MORE</div>

<footer class="footer abs">
  <div class="brand abs" style="left:111px;top:160px">VELMORA</div>

  <div class="foot-h abs" style="left:393px;top:76px">Glossary</div>
  <ul class="foot-links abs" style="left:393px;top:114px">
    <li>Praesenti</li><li>Voluptatum</li><li>Deleniti atque</li><li>Corrupti</li><li>Quos dolo</li>
  </ul>

  <div class="foot-h abs" style="left:576px;top:76px">Newsletter Subscription</div>
  <p class="abs" style="left:576px;top:116px;width:260px;font-size:14px;line-height:22px;color:#4c5660">Register your Email Address to get information about us</p>

  <div class="foot-h abs" style="left:877px;top:76px">Contact Us</div>
  <div class="contact-row abs" style="left:882px;top:116px">
    <svg width="10" height="16" viewBox="0 0 10 16" style="margin-top:6px"><path d="M5 0a5 5 0 0 1 5 5c0 4-5 11-5 11S0 9 0 5a5 5 0 0 1 5-5z" fill="#2f8fdf"/><circle cx="5" cy="5" r="2" fill="#fff"/></svg>
    <span>4207 Birchwell Ave. Suite #118<br>Lindenfield, ON, K9R 2T5</span>
  </div>
  <div class="contact-row abs" style="left:880px;top:196px">
    <svg width="13" height="13" viewBox="0 0 14 14" style="margin-top:8px"><path d="M3 0l3 3-2 2c1 2 3 4 5 5l2-2 3 3-2 3C6 14 0 8 0 3z" fill="#2f8fdf"/></svg>
    <span>1 555 014 2290</span>
  </div>
  <div class="contact-row abs" style="left:880px;top:250px">
    <svg width="14" height="11" viewBox="0 0 14 11" style="margin-top:9px"><rect width="14" height="11" rx="1" fill="#2f8fdf"/><path d="M1 1l6 5 6-5" stroke="#fff" stroke-width="1.4" fill="none"/></svg>
    <span>hello@velmora-care.com</span>
  </div>
</footer>
<div class="email-input abs">Email Address</div>
<div class="subscribe abs">SUBSCRIBE</div>
<div class="divider abs"></div>
<div class="abs" style="left:111px;top:3548px;font-size:13px;color:#4c5660">Copyrights © 2019, Velmora. All rights reserved.</div>
<div class="social abs" style="left:966px;top:3540px"></div>
<div class="social abs" style="left:1010px;top:3540px"></div>
<div class="social abs" style="left:1054px;top:3540px"></div>

</body>
</html>
```